I need a business card for my dumpster rentals business

We need a business card for a roll off dumpster business. We drop off the dumpster the customers fills it and we pick up and dispose of the materials. We want it simple but to the point. We will send images of what we like. We want black and red for the colors. We want stated on the card, (We bring it/ You fill it/ We dump it) uploaded some ideas I have came up with

```html
<!DOCTYPE html>
<html lang="en">
<head>
<meta charset="utf-8">
<title>Red Haul Dumpster Rentals – Business Card</title>
<link rel="stylesheet" href="https://fonts.googleapis.com/css2?family=Open+Sans:wght@400;600;700&display=swap">
<style>
  :root {
    --bg: #222222;
    --red: #e31b23;
    --red-deep: #b3171d;
    --black: #0b0b0b;
    --paper: #f4f4f4;
    --white: #ffffff;
    --ink: #111111;
  }
  * { box-sizing: border-box; margin: 0; padding: 0; }
  html, body { width: 1200px; height: 780px; overflow: hidden; }
  body {
    background: var(--bg);
    font-family: "Open Sans", Arial, sans-serif;
    position: relative;
  }
  .card {
    position: absolute;
    top: 230px;
    width: 540px;
    height: 310px;
    border-radius: 20px;
    overflow: hidden;
    box-shadow: 0 12px 30px rgba(0,0,0,0.45);
  }
  .card--front { left: 40px; background: var(--paper); }
  .card--back  { left: 620px; background: var(--red); }

  /* Wordmark */
  .wordmark { position: absolute; display: flex; align-items: center; gap: 10px; }
  .wordmark__text { display: flex; flex-direction: column; line-height: 1; }
  .wordmark__name { font-weight: 700; letter-spacing: -1px; }
  .wordmark__tag  { font-weight: 600; margin-top: 6px; }
  .wordmark__dot  { border-radius: 50%; flex: none; }

  .card--front .wordmark { left: 200px; top: 54px; }
  .card--front .wordmark__name { font-size: 54px; color: var(--ink); }
  .card--front .wordmark__tag  { font-size: 12px; letter-spacing: 7px; color: var(--red); }
  .card--front .wordmark__dot  { width: 28px; height: 28px; background: var(--red); }

  .card--back .wordmark { left: 22px; top: 20px; }
  .card--back .wordmark__name { font-size: 26px; color: var(--white); }
  .card--back .wordmark__tag  { font-size: 7px; letter-spacing: 3px; color: var(--white); margin-top: 3px; }

  /* Name band */
  .name-band {
    position: absolute;
    left: 0; top: 140px;
    width: 250px; height: 68px;
    background: var(--red);
    color: var(--white);
    padding: 8px 0 0 26px;
  }
  .name-band__name  { font-size: 23px; font-weight: 700; line-height: 1.15; }
  .name-band__title { font-size: 14px; font-weight: 400; padding-left: 14px; }

  /* Contact band */
  .contact-band {
    position: absolute;
    left: 250px; top: 190px;
    right: 0; height: 78px;
    background: var(--black);
    color: var(--white);
    padding: 8px 0 0 34px;
    font-size: 15px;
    line-height: 21px;
    list-style: none;
  }
  .contact-band li { display: flex; align-items: center; gap: 9px; }
  .contact-band svg { width: 12px; height: 12px; fill: var(--red); flex: none; }

  .address {
    position: absolute;
    left: 40px; top: 278px;
    font-size: 15px;
    color: var(--ink);
  }

  /* Back */
  .back-mark {
    position: absolute;
    right: -60px; bottom: -80px;
    width: 290px; height: 290px;
    border-radius: 50%;
    background: var(--red-deep);
    opacity: 0.55;
  }
  .service-line {
    position: absolute;
    left: 24px; bottom: 22px;
    font-size: 14px;
    font-weight: 600;
    color: var(--white);
    letter-spacing: 0.5px;
  }
</style>
</head>
<body>

<section class="card card--front" aria-label="Business card front">
  <div class="wordmark">
    <div class="wordmark__text">
      <span class="wordmark__name">Red Haul</span>
      <span class="wordmark__tag">DUMPSTER RENTALS</span>
    </div>
    <span class="wordmark__dot"></span>
  </div>

  <div class="name-band">
    <p class="name-band__name">Dana Whitlock</p>
    <p class="name-band__title">Managing Director</p>
  </div>

  <ul class="contact-band">
    <li>
      <svg viewBox="0 0 24 24" aria-hidden="true"><path d="M6.6 10.8a15 15 0 0 0 6.6 6.6l2.2-2.2c.3-.3.7-.4 1-.2 1.1.4 2.3.6 3.6.6.6 0 1 .4 1 1V20c0 .6-.4 1-1 1A17 17 0 0 1 3 4c0-.6.4-1 1-1h3.5c.6 0 1 .4 1 1 0 1.3.2 2.5.6 3.6.1.3 0 .7-.2 1z"/></svg>
      (555) 014-2276
    </li>
    <li>
      <svg viewBox="0 0 24 24" aria-hidden="true"><path d="M2 5h20v14H2zm2 2v.5l8 5 8-5V7z"/></svg>
      hello@redhaul.com
    </li>
    <li>
      <svg viewBox="0 0 24 24" aria-hidden="true"><circle cx="12" cy="12" r="10"/></svg>
      www.redhaul.com
    </li>
  </ul>

  <p class="address">480 Quarry Ln #12, Dayton, OH 45402, USA</p>
</section>

<section class="card card--back" aria-label="Business card back">
  <div class="wordmark">
    <div class="wordmark__text">
      <span class="wordmark__name">Red Haul</span>
      <span class="wordmark__tag">DUMPSTER RENTALS</span>
    </div>
  </div>
  <span class="back-mark"></span>
  <p class="service-line">We bring it / You fill it / We dump it</p>
</section>

</body>
</html>
```